Brightway Carpet and Tile cleaning Business card Design

I need a design that has the same feel as my van.
i would also like a prominent "Review us on facebook" somewhere, but not that it makes it look silly.
I would like the card to have a little bit of grey or black in the design as well.

It will need contact details
phone: 0455 817264
email: rkbrightwayclean@mailbox-example.com
website: www.brightwaycarpetandtilecleaning-example.com.au
facebook: /brightwaycarpetandtilecleaning

Industry/Entity Type

Business

Contact Information for Business Card

Phone number 0455817264
Email rkbrightwayclean@mailbox-example.com
Website www.brightwaycarpetandtilecleaning-example.com.au
Facebook/brightwaycarpetandtilecleaning

Colors
000000

Requirements
Must have
• Same feel as my van
• I want the card to stand out from the crowd
Nice to have
• Maybe include a tiny bit of a third colour? Grey's,blacks, orange?

```html
<!DOCTYPE html>
<html lang="en">
<head>
<meta charset="utf-8">
<title>Brightway Carpet and Tile Cleaning – Business Card</title>
<link rel="stylesheet" href="https://fonts.googleapis.com/css2?family=Arimo:wght@400;700&display=swap">
<style>
  :root {
    --ink: #000000;
    --paper: #ffffff;
    --leaf: #7cc24a;
    --leaf-soft: #8fcf5c;
    --sky: #29a9df;
    --steel: #6d6e70;
    --stage: #ececec;
    --text: #1a1a1a;
    --scene-a: #6f8f5a;
    --scene-b: #a9c6cf;
    --scene-c: #2aa6a8;
  }
  * { box-sizing: border-box; margin: 0; padding: 0; }
  html, body { width: 1189px; height: 1200px; overflow: hidden; }
  body {
    background: var(--stage);
    font-family: "Arimo", Arial, sans-serif;
    color: var(--text);
    position: relative;
  }
  .card {
    position: absolute;
    width: 764px;
    height: 435px;
    overflow: hidden;
    background: var(--ink);
    box-shadow: 0 6px 18px rgba(0,0,0,0.18);
  }
  .card--front { left: 315px; top: 130px; }
  .card--back  { left: 121px; top: 646px; }
  .card__art { position: absolute; inset: 0; width: 100%; height: 100%; }

  .brand { position: absolute; text-align: right; }
  .brand__name {
    display: flex; align-items: center; justify-content: flex-end; gap: 10px;
    font-weight: 700; color: var(--sky); line-height: 1;
  }
  .brand__dot { display: inline-block; border-radius: 50%; background: var(--sky); }
  .brand__tagline {
    color: var(--steel); letter-spacing: 0.18em; font-weight: 400; margin-top: 6px;
  }

  .card--front .brand { right: 60px; top: 108px; }
  .card--front .brand__name { font-size: 46px; }
  .card--front .brand__dot { width: 16px; height: 16px; }
  .card--front .brand__tagline { font-size: 16px; }

  .person { position: absolute; right: 36px; top: 214px; text-align: right; }
  .person__name { font-size: 25px; font-weight: 700; color: var(--ink); }
  .person__role { font-size: 18px; color: var(--leaf); margin-top: 2px; }

  .contacts { position: absolute; right: 36px; top: 286px; list-style: none; }
  .contacts__item {
    display: flex; align-items: center; justify-content: flex-end; gap: 7px;
    font-size: 17px; height: 27px; color: var(--text);
  }
  .contacts__icon {
    width: 21px; height: 21px; background: var(--leaf);
    display: inline-flex; align-items: center; justify-content: center; flex: none;
  }

  .card--back .brand { left: 240px; top: 190px; text-align: left; }
  .card--back .brand__name { font-size: 50px; justify-content: flex-start; }
  .card--back .brand__dot { width: 16px; height: 16px; }
  .card--back .brand__tagline { font-size: 17px; color: #4e4f51; }

  .services__title {
    position: absolute; right: 38px; top: 264px;
    font-size: 21px; font-weight: 700; color: var(--ink);
  }
  .services__list { position: absolute; list-style: none; top: 307px; }
  .services__list--left { right: 280px; }
  .services__list--right { right: 38px; }
  .services__item {
    display: flex; align-items: center; justify-content: flex-end; gap: 12px;
    font-size: 16px; height: 24.5px; color: var(--text);
  }
  .services__item::after {
    content: ""; width: 7px; height: 7px; border-radius: 50%; background: var(--sky);
  }
  .back-web {
    position: absolute; right: 39px; top: 393px; font-size: 17px; color: var(--text);
  }
</style>
</head>
<body>

<section class="card card--front" aria-label="Business card front">
  <svg class="card__art" viewBox="0 0 936 533" preserveAspectRatio="none" aria-hidden="true">
    <rect width="936" height="533" fill="var(--ink)"/>
    <ellipse cx="740" cy="100" rx="712" ry="522" fill="var(--paper)"/>
    <ellipse cx="740" cy="100" rx="704" ry="514" fill="var(--leaf)"/>
    <ellipse cx="740" cy="100" rx="670" ry="480" fill="var(--paper)"/>
    <path d="M780 533 Q870 515 936 462 L936 533 Z" fill="var(--leaf)"/>
    <path d="M815 533 Q885 518 936 482 L936 533 Z" fill="var(--ink)"/>
  </svg>

  <div class="brand">
    <div class="brand__name"><span class="brand__dot"></span>Brightway Clean</div>
    <div class="brand__tagline">CARPET &amp; TILE CLEANING</div>
  </div>

  <div class="person">
    <div class="person__name">Ryan Kessler</div>
    <div class="person__role">Managing/Director</div>
  </div>

  <ul class="contacts">
    <li class="contacts__item">0455 817264
      <span class="contacts__icon"><svg width="13" height="13" viewBox="0 0 24 24"><path fill="#fff" d="M6.6 10.8a15 15 0 0 0 6.6 6.6l2.2-2.2c.3-.3.7-.4 1-.2 1.1.4 2.3.6 3.6.6.6 0 1 .4 1 1V20c0 .6-.4 1-1 1A17 17 0 0 1 3 4c0-.6.4-1 1-1h3.5c.6 0 1 .4 1 1 0 1.3.2 2.5.6 3.6.1.3 0 .7-.2 1z"/></svg></span>
    </li>
    <li class="contacts__item">rkbrightwayclean@mailbox-example.com
      <span class="contacts__icon"><svg width="14" height="11" viewBox="0 0 14 11"><rect x="0.7" y="0.7" width="12.6" height="9.6" fill="none" stroke="#fff" stroke-width="1.4"/><path d="M1 1l6 5 6-5" fill="none" stroke="#fff" stroke-width="1.4"/></svg></span>
    </li>
    <li class="contacts__item">www.brightwaycarpetandtilecleaning-example.com.au
      <span class="contacts__icon"><svg width="14" height="14" viewBox="0 0 14 14" fill="none" stroke="#fff" stroke-width="1.2"><circle cx="7" cy="7" r="6"/><ellipse cx="7" cy="7" rx="2.6" ry="6"/><path d="M1 7h12M2 4h10M2 10h10"/></svg></span>
    </li>
    <li class="contacts__item">/brightwaycarpetandtilecleaning
      <span class="contacts__icon"></span>
    </li>
  </ul>
</section>

<section class="card card--back" aria-label="Business card back">
  <svg class="card__art" viewBox="0 0 936 533" preserveAspectRatio="none">
    <defs>
      <linearGradient id="sceneFade" x1="0" y1="0" x2="1" y2="0">
        <stop offset="0" stop-color="var(--scene-c)"/>
        <stop offset="0.3" stop-color="var(--scene-a)"/>
        <stop offset="0.55" stop-color="var(--scene-b)"/>
        <stop offset="0.85" stop-color="var(--paper)"/>
      </linearGradient>
    </defs>
    <rect width="936" height="533" fill="var(--ink)" aria-hidden="true"/>
    <ellipse cx="700" cy="820" rx="650" ry="870" fill="var(--paper)" aria-hidden="true"/>
    <ellipse cx="700" cy="820" rx="642" ry="862" fill="var(--leaf)" aria-hidden="true"/>
    <ellipse cx="700" cy="820" rx="612" ry="832" fill="url(#sceneFade)" role="img" aria-label="Photo of a smiling woman cleaning a window with a handheld squeegee, garden view behind"/>
  </svg>

  <div class="brand">
    <div class="brand__name"><span class="brand__dot"></span>Brightway Clean</div>
    <div class="brand__tagline">CARPET &amp; TILE CLEANING</div>
  </div>

  <h2 class="services__title">OUR SERVICES</h2>
  <ul class="services__list services__list--left">
    <li class="services__item">Pet Damage Repair</li>
    <li class="services__item">Flood Damage Repair</li>
    <li class="services__item">Carpet Repair</li>
  </ul>
  <ul class="services__list services__list--right">
    <li class="services__item">Carpet Cleaning</li>
    <li class="services__item">Tile and Grout Cleaning</li>
    <li class="services__item">Upholstery Cleaning</li>
  </ul>

  <p class="back-web">www.brightwaycarpetandtilecleaning-example.com.au</p>
</section>

</body>
</html>
```